Website Performance Testing eBook for the software testing industry

Overview:
I would like an ebook/whitepaper designed. This ebook will be digital published on my website as a lead generation piece. The purpose is to give high level tips on what to look for and things to think about when working on a website performance testing project.
The ebook also demonstrates our expertise and knowledge on the topic.
Topic:
This is an ebook on software testing. Specifically, website performance testing.
About Veltrana:
Veltrana Solutions is an outsourcing development and software testing firm, and we provide expert services for application development, testing and data analytics. We extend our clients’ software testing capabilities with on-demand technical expertise. Our quality assurance resources work as part of our clients’ teams to help test applications on time and within budget.
Our model is designed to allocate the right mix of local and offshore resources in order to optimize expertise, speed and cost. We provide the ability to quickly add specialty skills to our client’s development team without them incurring long-term costs. The result is far better management of resource capacities and outcomes.
Background on our branding and previous pieces:
I have included a few of our previous ebooks and whitepapers. I like the look and feel of these pieces, however we have made updates to our brand guidelines since them, so the new brand guidelines will need to be incorporated, and I'd like to refresh/update what we have done in the past.
Refer to our website for an idea of our look and feel. This page is one of our newer sections and would be a good reference:
http://www.veltranasol.example/data-analytics/
Tone and feel:
- The look and feel should be professional, clean and polished.
- I like good use of whitespace.
- I would prefer to keep stock photography of people to a minimum. Any images should add to the content and be relevant to the content.
(Also, I uploaded some InDesign files in case you wanted to refer to those assets, but I didn't include the Links folder because they were too big. If there's anything you more you need, let me know)
Target Market(s)
Audience:
The audience is senior Quality Assurance and Software Testing professionals.
- 30-45 years old
- Technical mindset
- Interested in learning
Titles include
- QA Lead
- QA Manager
- QA Director
- Director or VP of Development
- QA Automation Engineer
Our customers are medium to large sized companies. Many are software companies, but many are also enterprises in all almost all industries.

```html
<!DOCTYPE html>
<html lang="en">
<head>
<meta charset="utf-8">
<title>Website Performance Testing – Tools</title>
<link href="https://fonts.googleapis.com/css2?family=Open+Sans:wght@300;400;600;700&display=swap" rel="stylesheet">
<style>
  :root {
    --brand-red: #e8392b;
    --text-gray: #5b5b5b;
    --heading-gray: #b9bec6;
    --rule-gray: #cfcfcf;
    --page-bg: #ffffff;
  }
  html, body {
    margin: 0;
    padding: 0;
    width: 927px;
    height: 1200px;
    overflow: hidden;
    background: var(--page-bg);
  }
  .page {
    position: relative;
    width: 927px;
    height: 1200px;
    font-family: "Open Sans", Arial, sans-serif;
    color: var(--text-gray);
  }
  .running-head {
    position: absolute;
    left: 54px;
    top: 73px;
    font-size: 13px;
    font-weight: 400;
    color: var(--text-gray);
  }
  .brand-name {
    position: absolute;
    right: 66px;
    top: 68px;
    font-size: 22px;
    font-weight: 600;
    color: var(--brand-red);
    letter-spacing: -0.2px;
  }
  .head-rule {
    position: absolute;
    left: 54px;
    top: 109px;
    width: 819px;
    height: 1px;
    background: var(--rule-gray);
  }
  .title-bar {
    position: absolute;
    left: 97px;
    top: 166px;
    width: 2px;
    height: 106px;
    background: var(--brand-red);
  }
  .chapter-title {
    position: absolute;
    left: 125px;
    top: 193px;
    margin: 0;
    font-size: 37px;
    font-weight: 300;
    color: var(--brand-red);
    letter-spacing: -0.3px;
    white-space: nowrap;
  }
  .body-copy {
    position: absolute;
    left: 109px;
    width: 720px;
    margin: 0;
    font-size: 15px;
    font-weight: 300;
    line-height: 27.4px;
    color: var(--text-gray);
  }
  .body-copy.tight {
    left: 110px;
    width: 700px;
    line-height: 21px;
  }
  .tool-heading {
    position: absolute;
    left: 109px;
    margin: 0;
    font-size: 22px;
    font-weight: 700;
    color: var(--heading-gray);
    letter-spacing: 0.4px;
  }
  .page-number {
    position: absolute;
    left: 818px;
    top: 1123px;
    font-size: 15px;
    font-weight: 400;
    color: var(--brand-red);
  }
</style>
</head>
<body>
<div class="page">
  <header>
    <div class="running-head">Website Performance Testing</div>
    <div class="brand-name">Veltrana Solutions</div>
    <div class="head-rule"></div>
  </header>

  <div class="title-bar"></div>
  <h1 class="chapter-title">WEBSITE PERFORMANCE TESTING TOOLS</h1>

  <p class="body-copy" style="top:319px;">Many seasoned tools for testing websites exist on the market today. From simple page-load tools to advanced script-capable tool suites that test both client and server endpoints, there is something for everyone.</p>

  <p class="body-copy" style="top:443px;">Successful site testing also requires highly experienced testers who know these tools inside and out including specific techniques for load and stress tests that web testing software may not cover.</p>

  <h2 class="tool-heading" style="top:540px;">HEADCHECK</h2>

  <p class="body-copy" style="top:619px;">HeadCheck is one example of a class of online test tools that measure load times, find bottlenecks or suggest optimizations for HTTP traffic generated by your site. While it does not provide exhaustive performance analysis, it is useful for initial website analysis to find obvious pain points and for ongoing spot-check sanity checks as testing proceeds.</p>

  <h2 class="tool-heading" style="top:774px;">ARBOR LOADWRIGHT</h2>

  <p class="body-copy tight" style="top:856px;">This open-source downloadable tool is popular for website load and performance tests. It uses Corvet to simulate single and multiple servers. Many load test types are supported including HTTP/HTTPS, FTP, SQL, LDAP, Corvet and TestBrook. Other tools utilize Loadwright, such as CloudSurge which enables using Loadwright in</p>

  <div class="page-number">8</div>
</div>
</body>
</html>
```